Education Certificate

We need a modern yet professional Certificate for those who successfully pass / complete our online Training course.

There are various courses but ONE certificate design required.

the certificate needs to look extremely professional and of value.

```html
<!DOCTYPE html>
<html lang="en">
<head>
<meta charset="UTF-8">
<title>Certificate of Achievement</title>
<link href="https://fonts.googleapis.com/css2?family=Cormorant+Garamond:wght@500;600;700&family=Mulish:ital,wght@0,400;1,700&family=Playfair+Display:wght@700&family=Pinyon+Script&display=swap" rel="stylesheet">
<style>
  :root {
    --frame-blue: #a3bfdb;
    --pattern-blue: #c6d6e8;
    --line-blue: #5b86b4;
    --heading-blue: #2d5478;
    --body-blue: #4f7dab;
    --name-ink: #3a3a3a;
    --script-ink: #333;
    --seal-red: #7e1f2b;
    --paper: #ffffff;
  }
  html, body {
    margin: 0;
    padding: 0;
    width: 1200px;
    height: 855px;
    overflow: hidden;
    background: var(--frame-blue);
  }
  .certificate {
    position: relative;
    width: 1200px;
    height: 855px;
    background: var(--frame-blue);
  }
  .paper {
    position: absolute;
    left: 28px; top: 28px;
    width: 1144px; height: 799px;
    background: var(--paper);
  }
  .border-pattern {
    position: absolute;
    left: 34px; top: 34px;
    width: 1132px; height: 787px;
    box-sizing: border-box;
    border: 30px solid var(--pattern-blue);
  }
  .frame-line {
    position: absolute;
    box-sizing: border-box;
    border: 1.5px solid var(--line-blue);
  }
  .frame-line.outer { left: 64px; top: 64px; width: 1072px; height: 727px; }
  .frame-line.inner { left: 70px; top: 70px; width: 1060px; height: 715px; border-width: 1px; }
  .background-wave {
    position: absolute;
    left: 71px; top: 71px;
    width: 1058px; height: 713px;
    background: radial-gradient(ellipse at 25% 80%, rgba(190,212,232,0.35), transparent 60%),
                radial-gradient(ellipse at 80% 40%, rgba(190,212,232,0.3), transparent 55%);
  }
  .ornament {
    position: absolute;
    left: 510px;
    width: 180px;
    height: 34px;
    border-radius: 50%;
    background: linear-gradient(90deg, rgba(91,134,180,0.15), rgba(91,134,180,0.45), rgba(91,134,180,0.15));
  }
  .ornament.top { top: 93px; }
  .ornament.bottom { top: 253px; }
  .rule {
    position: absolute;
    left: 341px;
    width: 515px;
    height: 1.5px;
    background: var(--line-blue);
  }
  .rule.top { top: 127px; }
  .rule.bottom { top: 247px; }
  .centered {
    position: absolute;
    left: 0; right: 0;
    text-align: center;
    margin: 0;
  }
  .title {
    top: 134px;
    font-family: "Cormorant Garamond", serif;
    font-weight: 700;
    font-size: 54px;
    letter-spacing: 0.22em;
    padding-left: 0.22em;
    color: var(--heading-blue);
    line-height: 1;
  }
  .subtitle {
    top: 198px;
    font-family: "Cormorant Garamond", serif;
    font-weight: 700;
    font-size: 38px;
    letter-spacing: 0.14em;
    padding-left: 0.14em;
    color: var(--heading-blue);
    line-height: 1;
  }
  .body-text {
    font-family: "Mulish", sans-serif;
    font-weight: 400;
    font-size: 17px;
    color: var(--body-blue);
    line-height: 1.55;
  }
  .certify-line { top: 316px; }
  .recipient {
    top: 358px;
    font-family: "Playfair Display", serif;
    font-weight: 700;
    font-size: 40px;
    letter-spacing: 0.14em;
    padding-left: 0.14em;
    color: var(--name-ink);
    line-height: 1;
  }
  .achievement-line { top: 422px; }
  .course-title {
    top: 494px;
    font-family: "Mulish", sans-serif;
    font-style: italic;
    font-weight: 700;
    font-size: 22px;
    letter-spacing: 0.06em;
    color: var(--heading-blue);
    line-height: 1;
  }
  .award-line { top: 545px; }
  .signatory {
    position: absolute;
    left: 259px;
    width: 200px;
    text-align: center;
  }
  .signature-mark {
    margin: 0 auto;
    width: 86px;
    height: 54px;
    border-radius: 40% 60% 45% 55%;
    background: linear-gradient(120deg, rgba(60,60,60,0.08), rgba(60,60,60,0.18));
    position: absolute;
    left: 295px; top: 627px;
  }
  .signatory-name {
    top: 688px;
    font-family: "Cormorant Garamond", serif;
    font-weight: 600;
    font-size: 24px;
    color: var(--line-blue);
    line-height: 1;
  }
  .caption {
    font-family: "Cormorant Garamond", serif;
    font-weight: 500;
    font-size: 18px;
    color: var(--body-blue);
    line-height: 1;
    top: 720px;
  }
  .seal {
    position: absolute;
    left: 543px; top: 623px;
    width: 114px; height: 114px;
    border-radius: 50%;
    background: radial-gradient(circle at 45% 40%, #9a2a37, var(--seal-red) 70%);
  }
  .date-block {
    position: absolute;
    left: 720px;
    width: 260px;
    text-align: center;
  }
  .date-value {
    top: 654px;
    font-family: "Pinyon Script", cursive;
    font-size: 30px;
    color: var(--script-ink);
    line-height: 1;
  }
  .date-value sup { font-size: 14px; }
</style>
</head>
<body>
<main class="certificate">
  <div class="paper"></div>
  <div class="border-pattern" role="img" aria-label="Decorative scalloped guilloche border"></div>
  <div class="background-wave" role="img" aria-label="Faint guilloche wave pattern"></div>
  <div class="frame-line outer"></div>
  <div class="frame-line inner"></div>

  <div class="ornament top" role="img" aria-label="Scrolled fleur ornament"></div>
  <div class="rule top"></div>
  <h1 class="centered title">CERTIFICATE</h1>
  <h2 class="centered subtitle">OF ACHIEVEMENT</h2>
  <div class="rule bottom"></div>
  <div class="ornament bottom" role="img" aria-label="Scrolled fleur ornament"></div>

  <p class="centered body-text certify-line">This is to certify that</p>
  <p class="centered recipient">CLARA WHITMORE</p>
  <p class="centered body-text achievement-line">has successfully demonstrated proficient comprehension<br>In the course of</p>
  <p class="centered course-title">“MASTER HERBALIST DIPLOMA COURSE”</p>
  <p class="centered body-text award-line">And is therefore awarded this qualification with distinction</p>

  <div class="signature-mark" role="img" aria-label="Handwritten signature of the Director of Studies"></div>
  <p class="signatory signatory-name" style="margin:0">June Harlow</p>
  <p class="signatory caption" style="margin:0">Director of Studies</p>

  <div class="seal" role="img" aria-label="Red wax seal"></div>

  <p class="date-block date-value" style="margin:0">January 1<sup>st</sup> 2027</p>
  <p class="date-block caption" style="margin:0">Date</p>
</main>
</body>
</html>
```